Q.B. Brightpath Store

The design is for eCommerce home page but I would like it to complement this site: http://www.qbbrightpathsolutions.com/ but... it should also have independence as a standalone site.

The best design will be able to effectively mix corporate with a high quality small business consumer feel. It should be completely custom design, not a template look or feel. I want the users to get the feeling that this is the place to go for buying tech for business. We sell the same products as RVK.

You can be creative as you wish, as long as the elements of a great eCommerce site are present.

I would like your 'design' to blow these away:
http://www.shopping.zl.com/
mirabelo.com
http://www.rvk.com/

Here are references:
Call to action
http://markvantage.com/us/blog/48153-seven-tips-for-designing-an-effective-ecommerce-call-to-action

Effective Ecommerce design
http://www.vexa.com/ss/7-tips-for-effective-e-commerce#0

91 points of ecommerce
http://qir.com/blog/holygrail-of-ecommerce-conversion-optimization-91-points-checklist

UPDATE 07/11/2013:

Please look at the category sample png files. I see already many people are using the main menu from qbbrightpathsolutions.com and I do not mind your creativiety, but this is an eCommerce store and people need a menu to get to the categories and/or product types. I don't want to limit anyone creativity by the png samples. I'm also not using them to show I like them in any particular way or form, just that it's needed, whether it's a button (dropdown of course) that says 'Categories' or 'Products, whether it an accordion, horizontal or vertical.

Thanks

UPDATE 07/12/2013:

Please find other use of space that has been used for About Us paragraph (if you've added it to the page). About Us should have it's own page and the purpose of the design should be to sell products (and some services as products). Please put a link or some other creative method to lead users to the About Us page.

Reason: I've raised the award, including 1st, 2nd, and 3rd place and participation payments so I will also extend 7 days. Thanks!

I've updated the product brief. Please scroll down to where it says: UPDATE 07/11/2013

Thanks!

UPDATE 07/12/2013:

Please find other use of space that has been used for About Us paragraph (if you've added it to the page).  About Us should have it's own page and the purpose of the design should be to sell products (and some services as products). Please put a link or some other creative method to lead users to the About Us page if you must but not on the real estate of the page.

Thanks!

Added updates to the brief 7/14/2013.

Thanks!

The voting is in and the project is complete.  Thanks everyone for joining, all of those who participated are truly amazingly talented. But, there were only 3 prizes.  I will be having further projects down the line to develop other pages to this site after the initial implementation is completed.  I truly would like to have you all back. 

- Thank you.

Target Market(s)

corporate decision-makers AND small business consumers

Industry/Entity Type

Small Business

Requirements
Must have
• Call to action.
Openness (non-clutter).

These elements:
Search box
Logo
Tagline
Telephone number
Contact details
Address
My account / sign in
Shopping basket / checkout link
Latest offers
Promotional area
Email sign up
Delivery information
About us
Link to press office / corporate site
Terms and conditions
Sitemap for the footer.
Delivery offers: free
Personalized recommendations
Social media links
Accepted payment methods
Link to blog or community section
Change language / country

http://smartplansblog.pelloware.com/sales-leads-landing-page/

UPDATE 07/14/2013
Category Menu. This can be a dropdown, horizontal, vertical, etc. But shoppers need to know how to get to the products they want to buy.
Nice to have
• Trustmarks
Blog/Blog link

UPDATE 07/12/2013:
Make the footer useful.

UPDATE 07/14/2013 (Suggestions of elements to differentiate your designs)

-Quick Shop: A quick buy module/section: Where a user can put in a SKU number or Model number to quickly add the product to their shopping cart.

-Featured
-Best Sellers
-Specials
-Trending Tags/Tag Cloud
- Activity Stream
- Cross Sell/ Up Sell
- Testimonial
- Social Network Feed
- Live Help
- Feedback/Support/Contact Tab
- Show logged in user (i.e. Welcome, Mark Pelley)
Should not have
• The design SHOULD NOT be generic like this:

http://www.artgatherly.com/design/52392
http://www.falconmart.com/

The page should not feel over cluttered. It should not have low quality icons or design elements. Navigation should not be hard to discover or confusing.

```html
<!DOCTYPE html>
<html lang="en">
<head>
<meta charset="utf-8">
<title>Q.B. Brightpath Store</title>
<link rel="stylesheet" href="https://fonts.googleapis.com/css2?family=Open+Sans:wght@300;400;600;700&family=Arimo:wght@400;700&display=swap">
<style>
:root{
  --blue:#0c4f8f;
  --blue-dark:#083d70;
  --orange:#d9400f;
  --topbar:#2b2b2b;
  --text:#2a2a2a;
  --muted:#666;
  --footer-bg:#ededed;
  --panel:#e2e2e2;
  --line:#d7d7d7;
}
*{box-sizing:border-box;margin:0;padding:0}
html,body{width:922px;height:1200px;overflow:hidden;background:#fff}
body{position:relative;font-family:"Arimo",Arial,sans-serif;color:var(--text)}
.abs{position:absolute}
a{color:inherit;text-decoration:none}

/* top bar */
.topbar{left:0;top:0;width:922px;height:27px;background:var(--topbar)}
.topbar-links{position:absolute;right:78px;top:8px;font-size:9.6px;color:#fff;display:flex;gap:9px}
.topbar-links .sep{color:#bbb}

/* brand */
.brand{display:flex;align-items:center;gap:6px}
.brand-main{left:78px;top:46px}
.brand-dot{width:30px;height:30px;border-radius:50%;background:var(--blue);flex:none}
.brand-name{font-family:"Open Sans",sans-serif;font-weight:600;font-size:13.5px;color:var(--blue);line-height:1.1;letter-spacing:.4px;white-space:nowrap}

/* search */
.search{left:372px;top:54px;width:452px;height:29px;border:2px solid #cfcfcf;background:#fff;display:flex;align-items:center}
.search-input{flex:1;display:flex;align-items:center;gap:6px;padding-left:8px;font-size:10.5px;color:#999;height:100%}
.search-cat{width:80px;font-size:10px;color:#444;border-left:1px solid #ddd;height:17px;line-height:17px;padding-left:8px}
.search-btn{width:78px;height:23px;margin-right:2px;background:var(--blue);color:#fff;font-weight:700;font-size:10.5px;text-align:center;line-height:23px}

/* nav */
.mainnav{left:78px;top:110px;width:766px;height:31px;background:var(--blue);display:flex;border-radius:2px}
.mainnav a{color:#fff;font-size:10.8px;line-height:31px;padding:0 16px 0 13px;border-right:1px solid #6d93bd}
.mainnav a:last-child{border-right:0}

/* hero */
.hero{left:78px;top:141px;width:766px;height:293px;background:linear-gradient(90deg,#f5f4f2 0%,#ecebe8 40%,#dcd9d4 60%,#f0efed 100%)}
.hero-photo{left:470px;top:141px;width:374px;height:293px;
  background:
    radial-gradient(ellipse 90px 110px at 200px 110px,#d9b49b 0%,#c99c80 45%,rgba(201,156,128,0) 100%),
    radial-gradient(ellipse 130px 90px at 210px 300px,#1c2a40 0%,#243551 55%,rgba(36,53,81,0) 100%),
    radial-gradient(ellipse 60px 70px at 215px 260px,#f4f5f7 0%,rgba(244,245,247,0) 100%),
    linear-gradient(90deg,rgba(236,234,230,0) 0%,#d6d2cc 40%,#ece9e5 100%)}
.hero-title{left:102px;top:184px;font-family:"Open Sans",sans-serif;font-weight:600;font-size:26px;color:var(--orange);letter-spacing:.6px}
.hero-sub{left:105px;top:223px;font-family:"Open Sans",sans-serif;font-size:19.5px;color:var(--blue);line-height:26px}
.btn-learn{left:106px;top:322px;width:83px;height:27px;background:var(--orange);color:#fff;font-weight:700;font-size:11px;line-height:27px;text-align:center;border-radius:3px}
.dots{left:118px;top:402px;display:flex;gap:4px}
.dots span{width:10px;height:10px;border-radius:50%;background:#333}
.dots span.on{background:var(--blue)}

/* about */
.section-title{font-family:"Open Sans",sans-serif;font-size:28px;color:var(--blue);font-weight:300;white-space:nowrap}
.section-title b{color:var(--orange);font-weight:600}
.about-title{left:84px;top:468px}
.about-text{left:86px;top:509px;width:514px;font-size:10.3px;line-height:15.3px;color:#222}
.about-text p+p{margin-top:15px}
.more{left:538px;top:624px;font-size:8.5px;font-style:italic;color:var(--blue)}
.divider{left:616px;top:480px;height:152px;border-left:2px dotted #ccc}

/* signup */
.signup-title{left:632px;top:468px}
.field{left:635px;width:182px;height:26px;background:#ebebeb;border:1px solid #d4d4d4;font-size:10px;color:#555;padding-left:6px;line-height:24px}
.forgot{left:639px;top:607px;font-size:10.5px;color:var(--orange);font-weight:700}
.btn-login{left:750px;top:602px;width:67px;height:24px;background:var(--blue);color:#fff;font-weight:700;font-size:11px;line-height:24px;text-align:center;border-radius:3px}

/* products */
.product{top:682px;width:159px;height:209px;border:1px solid var(--line);background:#fff;box-shadow:0 0 8px rgba(0,0,0,.06)}
.product-img{position:absolute;left:6px;top:6px;width:145px;height:111px}
.product-desc{position:absolute;left:7px;top:124px;width:146px;font-size:9px;line-height:14px;color:#333}
.product-price{position:absolute;left:8px;top:156px;font-family:"Open Sans",sans-serif;font-weight:600;font-size:13.5px;color:var(--orange);letter-spacing:.5px}
.product-actions{position:absolute;left:8px;top:179px;display:flex}
.btn-buy{width:78px;height:23px;background:var(--blue);color:#fff;font-size:8.5px;font-weight:700;display:flex;align-items:center;gap:6px;padding-left:6px}
.btn-details{width:64px;height:23px;background:#e6e6e6;color:var(--blue);font-size:8.5px;font-weight:700;display:flex;align-items:center;gap:4px;padding-left:4px}

/* footer */
.footer-bar{left:0;top:956px;width:922px;height:30px;background:var(--blue);color:#fff;font-size:9.2px}
.footer-bar .links{position:absolute;top:10px;display:flex}
.footer-bar .links a{padding:0 6px;border-right:1px solid #6d93bd}
.footer-bar .links a:first-child{padding-left:0}
.footer-bar .links a:last-child{border-right:0}
.footer-bg{left:0;top:986px;width:922px;height:214px;background:var(--footer-bg)}
.social{top:998px;width:29px;height:29px}
.footer-brand{left:670px;top:996px}
.footer-panel{top:1040px;height:113px;background:var(--panel);border-radius:3px}
.col-title{font-family:"Open Sans",sans-serif;font-weight:600;font-size:11.5px;color:var(--orange)}
.col-links{font-size:9px;line-height:12.3px;color:#555}
.pay{width:34px;height:22px;border-radius:2px;border:1px solid #c8c8c8}
.contact{left:688px;font-size:9px;line-height:11px;color:#444}
.copyright{left:92px;top:1173px;font-size:9px;color:#333}
</style>
</head>
<body>

<div class="abs topbar">
  <nav class="topbar-links">
    <a href="#">Shop</a><span class="sep">|</span>
    <a href="#">My Account</a><span class="sep">|</span>
    <a href="#">Checkout</a><span class="sep">|</span>
    <a href="#">My Shopping</a><span class="sep">|</span>
    <a href="#">Cart:0 items</a>
  </nav>
</div>

<div class="abs brand brand-main">
  <span class="brand-dot"></span>
  <span class="brand-name">Q.B. BRIGHTPATH<br>SOLUTIONS</span>
</div>

<div class="abs search">
  <div class="search-input">
    <svg width="11" height="11" viewBox="0 0 12 12"><circle cx="5" cy="5" r="3.8" fill="none" stroke="#555" stroke-width="1.5"/><line x1="8" y1="8" x2="11" y2="11" stroke="#555" stroke-width="1.6"/></svg>
    Search
  </div>
  <div class="search-cat">Categories ▾</div>
  <div class="search-btn">SEARCH</div>
</div>

<nav class="abs mainnav">
  <a href="#">Home</a>
  <a href="#">Small Business</a>
  <a href="#">Latest offers</a>
  <a href="#">Enterprise</a>
  <a href="#">Non-Profit</a>
  <a href="#">Contact Us</a>
</nav>

<div class="abs hero"></div>
<div class="abs hero-photo" role="img" aria-label="Photo of a smiling businesswoman in a dark suit and white shirt, office blurred behind"></div>
<div class="abs hero-title">BRIGHTPATH SOLUTIONS</div>
<div class="abs hero-sub">Should you CHOOSE TO HAVE<br>A customized greeting on your<br>ACCOUNT, WE WILL NOT .</div>
<a class="abs btn-learn" href="#">Learn More »</a>
<div class="abs dots"><span></span><span class="on"></span><span></span><span></span></div>

<h2 class="abs section-title about-title">Who we Are and <b>How We Work</b></h2>
<div class="abs about-text">
  <p>Lorem Ipsum is simply dummy text of the printing and typesetting industry. Lorem Ipsum has been the industry's standard dummy text ever since the 1500s, when an unknown printer took a galley of type and scrambled it to make a type specimen book. It has survived not only five centuries, but also the leap into electronic typesetting, remaining essentially unchanged. It was popularised in the 1960s with</p>
  <p>The release of Lettrix sheets containing Lorem Ipsum passages, and more recently with desktop publishing software like Orvel PageCraft including versions of Lorem Ipsum.</p>
</div>
<a class="abs more" href="#">More Details »</a>
<div class="abs divider"></div>

<h2 class="abs section-title signup-title">Email <b>Sign Up</b></h2>
<div class="abs field" style="top:518px">Username</div>
<div class="abs field" style="top:556px">Password</div>
<a class="abs forgot" href="#">Forgot Password ?</a>
<a class="abs btn-login" href="#">LOGIN »</a>

<div class="abs product" style="left:87px">
  <div class="product-img" role="img" aria-label="Black rack-mount server unit" style="background:radial-gradient(ellipse at center,#3a3a3a 0%,#6d6d6d 40%,#f6f6f6 72%)"></div>
  <div class="product-desc">simply dummy text of the printing and typesetting industry.</div>
  <div class="product-price">$45.00</div>
  <div class="product-actions">
    <a class="btn-buy" href="#"><svg width="14" height="12" viewBox="0 0 14 12"><path d="M1 1h2l2 7h7l1-5H4" fill="none" stroke="#fff" stroke-width="1.4"/><circle cx="6" cy="10.5" r="1.2" fill="#fff"/><circle cx="11" cy="10.5" r="1.2" fill="#fff"/></svg>BUY NOW</a>
    <a class="btn-details" href="#"><svg width="12" height="12" viewBox="0 0 12 12"><circle cx="5" cy="5" r="3.6" fill="none" stroke="#0c4f8f" stroke-width="1.5"/><line x1="7.8" y1="7.8" x2="11" y2="11" stroke="#0c4f8f" stroke-width="1.8"/></svg>DETAILS</a>
  </div>
</div>
<div class="abs product" style="left:278px">
  <div class="product-img" role="img" aria-label="Black desk IP telephone" style="background:radial-gradient(ellipse at center,#2e2e2e 0%,#7a7a7a 45%,#eeeeee 75%)"></div>
  <div class="product-desc">simply dummy text of the printing and typesetting industry.</div>
  <div class="product-price">$45.00</div>
  <div class="product-actions">
    <a class="btn-buy" href="#"><svg width="14" height="12" viewBox="0 0 14 12"><path d="M1 1h2l2 7h7l1-5H4" fill="none" stroke="#fff" stroke-width="1.4"/><circle cx="6" cy="10.5" r="1.2" fill="#fff"/><circle cx="11" cy="10.5" r="1.2" fill="#fff"/></svg>BUY NOW</a>
    <a class="btn-details" href="#"><svg width="12" height="12" viewBox="0 0 12 12"><circle cx="5" cy="5" r="3.6" fill="none" stroke="#0c4f8f" stroke-width="1.5"/><line x1="7.8" y1="7.8" x2="11" y2="11" stroke="#0c4f8f" stroke-width="1.8"/></svg>DETAILS</a>
  </div>
</div>
<div class="abs product" style="left:469px">
  <div class="product-img" role="img" aria-label="Silver network gateway box" style="background:radial-gradient(ellipse at center,#c9ccd2 0%,#8f99a8 40%,#e8ebef 75%)"></div>
  <div class="product-desc">simply dummy text of the printing and typesetting industry.</div>
  <div class="product-price">$45.00</div>
  <div class="product-actions">
    <a class="btn-buy" href="#"><svg width="14" height="12" viewBox="0 0 14 12"><path d="M1 1h2l2 7h7l1-5H4" fill="none" stroke="#fff" stroke-width="1.4"/><circle cx="6" cy="10.5" r="1.2" fill="#fff"/><circle cx="11" cy="10.5" r="1.2" fill="#fff"/></svg>BUY NOW</a>
    <a class="btn-details" href="#"><svg width="12" height="12" viewBox="0 0 12 12"><circle cx="5" cy="5" r="3.6" fill="none" stroke="#0c4f8f" stroke-width="1.5"/><line x1="7.8" y1="7.8" x2="11" y2="11" stroke="#0c4f8f" stroke-width="1.8"/></svg>DETAILS</a>
  </div>
</div>
<div class="abs product" style="left:661px">
  <div class="product-img" role="img" aria-label="Black 2U rack server chassis" style="background:radial-gradient(ellipse at center,#333 0%,#777 38%,#f7f7f7 70%)"></div>
  <div class="product-desc">simply dummy text of the printing and typesetting industry.</div>
  <div class="product-price">$45.00</div>
  <div class="product-actions">
    <a class="btn-buy" href="#"><svg width="14" height="12" viewBox="0 0 14 12"><path d="M1 1h2l2 7h7l1-5H4" fill="none" stroke="#fff" stroke-width="1.4"/><circle cx="6" cy="10.5" r="1.2" fill="#fff"/><circle cx="11" cy="10.5" r="1.2" fill="#fff"/></svg>BUY NOW</a>
    <a class="btn-details" href="#"><svg width="12" height="12" viewBox="0 0 12 12"><circle cx="5" cy="5" r="3.6" fill="none" stroke="#0c4f8f" stroke-width="1.5"/><line x1="7.8" y1="7.8" x2="11" y2="11" stroke="#0c4f8f" stroke-width="1.8"/></svg>DETAILS</a>
  </div>
</div>

<div class="abs footer-bar">
  <nav class="links" style="left:92px">
    <a href="#">Site Map</a><a href="#">Search Terms</a><a href="#">Advanced Search</a><a href="#">Orders and Returns</a><a href="#">Contact Us</a>
  </nav>
  <nav class="links" style="right:96px">
    <a href="#">Custom Link</a><a href="#">About Us</a><a href="#">Customer Service</a>
  </nav>
</div>
<div class="abs footer-bg"></div>

<a class="abs social" href="#" style="left:94px;background:#3b5a98" aria-label="Social network 1"></a>
<a class="abs social" href="#" style="left:138px;background:#2aa8e0" aria-label="Social network 2"></a>
<a class="abs social" href="#" style="left:184px;background:#dd4b39" aria-label="Social network 3"></a>
<a class="abs social" href="#" style="left:228px;background:#c4302b" aria-label="Social network 4"></a>

<div class="abs brand footer-brand">
  <span class="brand-dot"></span>
  <span class="brand-name">Q.B. BRIGHTPATH<br>SOLUTIONS</span>
</div>

<div class="abs footer-panel" style="left:92px;width:569px"></div>
<div class="abs footer-panel" style="left:670px;width:156px"></div>

<div class="abs col-title" style="left:114px;top:1050px">Customer Service</div>
<div class="abs col-links" style="left:117px;top:1072px">Delivery<br>Shipping Methods<br>Payment<br>Returns &amp; Refund<br>Customers</div>

<div class="abs col-title" style="left:280px;top:1050px">What's in Store</div>
<div class="abs col-links" style="left:281px;top:1074px">Women<br>Men<br>Products A-Z<br>Our Brands<br>Buy a Gift Card</div>

<div class="abs col-title" style="left:418px;top:1052px">Other Sites</div>
<div class="abs col-links" style="left:419px;top:1076px">Second Site<br>Social Funpage<br>Microblog<br>Circles Plus<br>Video Channel</div>

<div class="abs col-title" style="left:537px;top:1050px">Easy payment</div>
<div class="abs pay" style="left:536px;top:1080px;background:#f4f4f4"></div>
<div class="abs pay" style="left:575px;top:1080px;background:#e58a2c"></div>
<div class="abs pay" style="left:614px;top:1080px;background:#f1f1f1"></div>
<div class="abs pay" style="left:536px;top:1108px;background:#2b77b9"></div>
<div class="abs pay" style="left:575px;top:1108px;background:#dcdcdc"></div>
<div class="abs pay" style="left:614px;top:1108px;background:#f5c518"></div>

<div class="abs col-title" style="left:688px;top:1051px">Contact us</div>
<div class="abs contact" style="top:1078px;font-size:10.5px;font-weight:700;color:#555">+001 (000) 555 247</div>
<div class="abs contact" style="top:1095px">Company Inc.<br>42 Harlow Street<br>Fairview, NY 041, USA</div>

<div class="abs copyright">Copyright © 2012 Brightpath Solution. All Rights Reserved.</div>

</body>
</html>
```